KBT Business Cards

We require business cards for our business. We would like a matte black back to the card, with our logo centred in the middle. The front side of the card is open to design.

Target Market(s)

Clients looking for legal services (professional)

Industry/Entity Type

Legal

Contact Information for Business Card

Doran Kelbrath
Partner
Mobile: 0461 738 524
Email: doran@kbtlaw.co
Website: www.kbtlaw.co
Level 3, 118 Wendmore Street
Sydney NSW 2000

Font styles to use
Other font styles liked:
• Avenir

Colors
f04a50
ffffff
1b1b1b

Requirements
Must have
• Black back with logo included in the centre of the card.
• Our font is Avenir.

```html
<!DOCTYPE html>
<html lang="en">
<head>
<meta charset="utf-8">
<title>KBT Legal – Business Cards</title>
<link rel="stylesheet" href="https://fonts.googleapis.com/css2?family=Lato:wght@400;700;900&display=swap">
<style>
  :root {
    --stage: #dedede;
    --card-white: #ffffff;
    --ink: #1b1b1b;
    --matte-black: #1b1b1b;
    --crimson: #cc2049;
    --on-dark: #ffffff;
  }
  * { box-sizing: border-box; margin: 0; padding: 0; }
  html, body {
    width: 1200px;
    height: 900px;
    overflow: hidden;
  }
  body {
    background: var(--stage);
    font-family: "Lato", sans-serif;
    position: relative;
  }
  .card {
    position: absolute;
    width: 520px;
    height: 300px;
    border-radius: 26px;
    box-shadow: 0 6px 18px rgba(0, 0, 0, 0.14);
  }

  /* Front: white card with wordmark and address */
  .card--front {
    left: 110px;
    top: 120px;
    background: var(--card-white);
    color: var(--ink);
  }
  .front-mark {
    position: absolute;
    left: 0;
    right: 0;
    top: 96px;
    display: flex;
    align-items: center;
    justify-content: center;
    gap: 16px;
  }
  .front-mark__square {
    width: 34px;
    height: 34px;
    background: var(--crimson);
  }
  .front-mark__name {
    font-weight: 900;
    font-size: 40px;
    letter-spacing: 2px;
    line-height: 1;
    color: var(--ink);
  }
  .front-address {
    position: absolute;
    left: 0;
    right: 0;
    bottom: 40px;
    text-align: center;
    font-size: 15px;
    letter-spacing: 0.4px;
    color: var(--ink);
  }

  /* Back: matte black card with centred mark and contact details */
  .card--back {
    left: 570px;
    top: 470px;
    background: var(--matte-black);
    color: var(--on-dark);
    text-align: center;
  }
  .back-mark {
    position: absolute;
    left: 0;
    right: 0;
    top: 46px;
    font-weight: 900;
    font-size: 54px;
    letter-spacing: 4px;
    line-height: 1;
  }
  .back-person {
    position: absolute;
    left: 0;
    right: 0;
    top: 140px;
  }
  .back-person__name {
    font-weight: 700;
    font-size: 20px;
    letter-spacing: 0.8px;
    text-transform: uppercase;
  }
  .back-person__role {
    font-size: 14px;
    margin-top: 2px;
  }
  .back-rule {
    width: 170px;
    height: 1px;
    margin: 10px auto;
    background: var(--on-dark);
  }
  .back-contact {
    font-size: 14px;
    line-height: 1.5;
  }
  .back-contact b { font-weight: 900; }
</style>
</head>
<body>
  <section class="card card--front" aria-label="Card front">
    <div class="front-mark">
      <span class="front-mark__square"></span>
      <span class="front-mark__name">KBT LEGAL</span>
    </div>
    <p class="front-address">Level 3, 118 Wendmore Street Sydney NSW 2000</p>
  </section>

  <section class="card card--back" aria-label="Card back">
    <div class="back-mark">KBT</div>
    <div class="back-person">
      <p class="back-person__name">Doran Kelbrath</p>
      <p class="back-person__role">Partner</p>
      <div class="back-rule"></div>
      <p class="back-contact"><b>M:</b> 0461 738 524 | <b>E:</b> doran@kbtlaw.co</p>
      <p class="back-contact"><b>W:</b> www.kbtlaw.co</p>
    </div>
  </section>
</body>
</html>
```